New Business Card Design Project

We require a business card design for Vexalund, a newly established Indian company.
Our focus is on the development, manufacturing, and export of a diverse array of pharmaceutical products on a global scale. The card should convey a professional appearance, as our primary markets are in Africa, China, and Southeast Asian nations.
We envision a two-sided business card, with the reverse side dedicated to a logo set against a solid color or an elegantly designed pattern. The corners should be rounded. We would appreciate seeing both horizontal and vertical design options. We trust the designer to utilize their expertise in creating this design.

The content for the business card is included in the attached Word file.

Target Market(s)

Our primary markets are in Africa, China, and Southeast Asian, Latin America, Maldives, Sri Lanka

Industry/Entity Type

Pharmaceutical Manufacturing and Export

Contact Information for Business Card

Colors

Designer to choose colors to be used in the design.

Requirements
Must have
• The reverse side of the business card features solely the logo along with the tagline, "Care for Every Day."
Should not have
• The logo should not exceed two instances, encompassing both the front and back sides of the card.

```html
<!DOCTYPE html>
<html lang="en">
<head>
<meta charset="utf-8">
<title>Vexalund Business Card</title>
<link rel="stylesheet" href="https://fonts.googleapis.com/css2?family=Montserrat:wght@800&family=Open+Sans:wght@300;400;600;800&display=swap">
<style>
  :root {
    --stage: #222223;
    --card: #1c1c1d;
    --blue: #2ea8e0;
    --coral: #f0634e;
    --white: #ffffff;
  }
  * { margin: 0; padding: 0; box-sizing: border-box; }
  html, body { width: 1200px; height: 711px; overflow: hidden; }
  body { background: var(--stage); position: relative; font-family: "Open Sans", sans-serif; }

  .card {
    position: absolute;
    top: 200px;
    width: 540px;
    height: 310px;
    background: var(--card);
    border-radius: 18px;
    overflow: hidden;
    box-shadow: 0 14px 30px rgba(0,0,0,.55);
  }
  .card--back { left: 40px; border-bottom: 4px solid var(--blue); }
  .card--front { left: 620px; }

  /* back side */
  .back-brand {
    position: absolute;
    left: 0; right: 0; top: 108px;
    display: flex; align-items: center; justify-content: center; gap: 14px;
  }
  .brand-dot { width: 26px; height: 26px; border-radius: 50%; background: var(--coral); }
  .wordmark {
    font-family: "Montserrat", sans-serif;
    font-weight: 800;
    color: var(--blue);
    letter-spacing: 1px;
    line-height: 1;
  }
  .back-brand .wordmark { font-size: 62px; }
  .tagline {
    position: absolute;
    top: 190px; right: 128px;
    color: var(--white);
    font-size: 14px;
    letter-spacing: .8px;
  }

  /* front side */
  .front-wave { position: absolute; inset: 0; }
  .front-brand {
    position: absolute; left: 36px; top: 48px;
    display: flex; align-items: center; gap: 10px;
  }
  .front-brand .brand-dot { width: 18px; height: 18px; }
  .front-brand .wordmark { font-size: 42px; }

  .person { position: absolute; right: 36px; top: 26px; text-align: right; }
  .person__name { color: var(--blue); font-size: 25px; font-weight: 300; letter-spacing: .8px; }
  .person__name strong { font-weight: 800; }
  .person__title { color: var(--white); font-size: 14px; margin-top: -2px; }
  .person-bar { position: absolute; right: 0; top: 24px; width: 16px; height: 54px; background: var(--blue); }

  .contact { position: absolute; left: 40px; top: 170px; list-style: none; }
  .contact li {
    display: flex; align-items: center; gap: 10px;
    color: var(--white); font-size: 14px; letter-spacing: .5px;
    margin-bottom: 6px;
  }
  .contact svg { width: 16px; height: 16px; flex: none; }

  .address {
    position: absolute; right: 30px; bottom: 46px;
    color: var(--white); font-size: 13.5px; line-height: 1.45;
    text-align: right; letter-spacing: .4px;
  }
</style>
</head>
<body>

  <section class="card card--back">
    <div class="back-brand">
      <span class="brand-dot"></span>
      <span class="wordmark">Vexalund</span>
    </div>
    <p class="tagline">Care for Every Day.</p>
  </section>

  <section class="card card--front">
    <svg class="front-wave" viewBox="0 0 540 310" preserveAspectRatio="none" aria-hidden="true">
      <path d="M0,310 L0,292 C190,300 300,262 370,190 C420,140 470,112 540,104 L540,310 Z" fill="var(--blue)"/>
      <path d="M0,262 C120,278 250,262 330,214 C260,258 140,282 0,276 Z" fill="var(--coral)"/>
    </svg>

    <div class="front-brand">
      <span class="brand-dot"></span>
      <span class="wordmark">Vexalund</span>
    </div>

    <div class="person">
      <p class="person__name"><strong>Rohan</strong> K. Malvi</p>
      <p class="person__title">CEO</p>
    </div>
    <span class="person-bar"></span>

    <ul class="contact">
      <li>
        <svg viewBox="0 0 16 16" aria-hidden="true"><rect x="4" y="1.5" width="8" height="13" rx="1.5" fill="none" stroke="var(--coral)" stroke-width="1.5"/></svg>
        +919 310457182
      </li>
      <li>
        <svg viewBox="0 0 16 16" aria-hidden="true"><circle cx="8" cy="8" r="6.5" fill="none" stroke="var(--blue)" stroke-width="1.5"/><path d="M1.5 8h13M8 1.5c-3 3-3 10 0 13M8 1.5c3 3 3 10 0 13" fill="none" stroke="var(--blue)" stroke-width="1.1"/></svg>
        www.vexalund.com
      </li>
      <li>
        <svg viewBox="0 0 16 16" aria-hidden="true"><rect x="1.5" y="3.5" width="13" height="9" rx="1" fill="none" stroke="var(--coral)" stroke-width="1.5"/><path d="M1.5 4l6.5 5 6.5-5" fill="none" stroke="var(--coral)" stroke-width="1.5"/></svg>
        rmalvi@vexalund.com
      </li>
    </ul>

    <p class="address">12, Sarovar Colony,<br>Nandgaon, 431204, India</p>
  </section>

</body>
</html>
```